Set of 6 Illustrations for Transport Security Platform – Duvrelt

Duvrelt is an innovative solution that enhances safety in transport and logistics, based on identity verification, access control, and collaboration within a network of verified subcontractors.
The purpose of the graphics is to present the system’s key functionalities in a modern, technological way that aligns with the brand’s visual identity.
The website will feature a clean and bright aesthetic:
Background: white or light gray (#f7f7f7)
Text: black or dark gray (#1a1a1a)
Accent color: green (#27ae60 or #2ecc71) – symbolizing safety and trust
The graphics should be stylistically consistent, simple, and easy to read — ideally created in a flat design or isometric 3D style with subtle gradients.
We should avoid stock photos of people or trucks — the goal is a symbolic and technological visual approach.
I initially prepared the graphics myself in Canva, but they are not visually consistent.
Colors
Designer to choose only greyscale colors for use in the design.
Look and feel
Each slider illustrates characteristics of the customer's brand and the style your logo design should communicate.

```html
<!DOCTYPE html>
<html lang="en">
<head>
<meta charset="utf-8">
<title>Duvrelt – Verification Flow</title>
<link href="https://fonts.googleapis.com/css2?family=Poppins:wght@400;500;600;700&family=Oswald:wght@500;600&display=swap" rel="stylesheet">
<style>
:root{
  --green:#27ae60;
  --green-soft:#7dc77f;
  --chip-soft:#6fbf73;
  --pill-grey:#e2ebe2;
  --stage:#f1f1f1;
  --ink:#1a1a1a;
  --ink-soft:#333;
  --white:#fff;
}
*{box-sizing:border-box;margin:0;padding:0}
html,body{width:1200px;height:794px;overflow:hidden;background:var(--white)}
body{font-family:"Poppins",sans-serif;color:var(--ink);position:relative}
.stage{position:absolute;left:73px;top:117px;width:762px;height:596px;background:var(--stage);border-radius:100px}
.links{position:absolute;left:0;top:0;width:1200px;height:794px}
.card{position:absolute;background:var(--white);border:2.5px solid var(--green);border-radius:11px}
.abs{position:absolute}
.step-title{font-weight:700;font-size:16px}
.name{font-weight:600;font-size:13px}
.status-row{position:absolute;left:10px;top:15px;display:flex;align-items:center;gap:6px;z-index:2}
.stamp{font-family:"Oswald",sans-serif;font-weight:600;font-size:14px;color:var(--green);border-left:3px solid var(--ink-soft);border-right:3px solid var(--ink-soft);border-radius:5px;padding:0 3px;line-height:26px;white-space:nowrap}
.stamp.dark{color:var(--ink-soft)}
.stamp.light{position:absolute;color:var(--white);border-color:var(--white);font-size:21px;line-height:33px;padding:0 5px}
.figure-fill{position:absolute;background:var(--green);border-radius:4px}
.details{position:absolute;right:6px;bottom:-3px;height:27px;padding:0 12px 0 6px;background:var(--green);color:var(--white);border-radius:14px 14px 4px 14px;font-family:"Oswald",sans-serif;font-weight:500;font-size:15px;display:flex;align-items:center;gap:5px}
.details .dots{width:13px;height:13px;border-radius:50%;background:var(--white);display:flex;align-items:center;justify-content:center;gap:1.5px}
.details .dots i{width:2px;height:2px;border-radius:50%;background:var(--green);display:block}
.pill-btn{position:absolute;background:var(--green);color:var(--white);border-radius:18px;font-weight:600;font-size:12.5px;display:flex;align-items:center;justify-content:center;gap:8px}
.start-tab{position:absolute;left:172px;top:187px;width:73px;height:27px;background:var(--green);color:var(--white);border-radius:12px 12px 0 0;font-weight:600;font-size:11.5px;text-align:center;line-height:27px}
.check{position:absolute;left:123px;top:411px;width:171px;height:229px;background:var(--green);border-radius:18px}
.check-title{position:absolute;left:6px;top:8px;width:159px;height:36px;background:var(--white);border-radius:18px;text-align:center;line-height:36px;font-weight:600;font-size:13px}
.check-list{position:absolute;left:18px;top:56px;list-style:none}
.check-list li{display:flex;align-items:center;gap:10px;height:39px;color:var(--white);font-weight:600;font-size:13.5px;line-height:13.5px}
.check-list .ico{width:30px;height:30px;flex:none}
.data{position:absolute;left:0;width:100%;text-align:center;font-size:12.5px;line-height:16px}
.data b{font-weight:600}
.chip{position:absolute;left:7px;padding:0 5px;border-radius:4px;font-weight:600;font-size:13px;line-height:18px}
.grey-pill{position:absolute;left:7px;width:156px;height:35px;background:var(--pill-grey);border-radius:16px;text-align:center;font-weight:600;font-size:12.5px;line-height:13.5px;display:flex;align-items:center;justify-content:center}
.next-tab{position:absolute;left:47px;bottom:-3px;width:73px;height:27px;background:var(--green);color:var(--white);border-radius:13px 13px 0 0;font-family:"Oswald",sans-serif;font-weight:500;font-size:15px;display:flex;align-items:center;justify-content:center;gap:6px}
.plant-pill{position:absolute;left:6px;top:82px;width:156px;height:35px;border:2.5px solid var(--green);border-radius:18px;color:var(--green);font-weight:600;font-size:12.5px;display:flex;align-items:center;justify-content:center}
.pass{position:absolute;left:871px;top:575px;width:257px;height:163px;background:var(--green);border-radius:13px;color:var(--white)}
.pass-lines{position:absolute;left:11px;top:55px;font-size:13.5px;line-height:16.2px}
.pass-lines b{font-weight:600;color:#111}
.gps{position:absolute;right:18px;top:16px;text-align:center;font-family:"Oswald",sans-serif;font-size:9px}
.id-card{position:absolute;left:161px;top:92px;width:78px;height:53px;background:var(--white);border-radius:3px}
</style>
</head>
<body>

<div class="stage"></div>

<svg class="links" viewBox="0 0 1200 794" aria-hidden="true">
  <g fill="none" stroke="#7dc77f" stroke-width="8" stroke-linejoin="round" stroke-linecap="butt">
    <path d="M293 273 H327 V485 H367"/>
    <path d="M452 355 V391"/>
    <path d="M452 372 H577 V290 H615"/>
    <path d="M541 490 H580 V405 H615"/>
    <path d="M452 513 V539"/>
    <path d="M790 385 H835 V468 H870"/>
    <path d="M954 292 V349"/>
    <path d="M1000 519 V575"/>
  </g>
</svg>

<!-- Step 1 -->
<div class="start-tab">Start</div>
<div class="card" style="left:121px;top:212px;width:172px;height:142px">
  <div class="abs step-title" style="left:15px;top:12px">Step 1</div>
  <div class="figure-fill" role="img" aria-label="Warehouse building icon" style="left:58px;top:54px;width:54px;height:28px"></div>
  <div class="pill-btn" style="left:6px;top:96px;width:156px;height:35px">COMPANY FINDER
    <svg width="16" height="17" viewBox="0 0 16 17"><circle cx="6.5" cy="6.5" r="5" fill="none" stroke="#fff" stroke-width="1.6"/><path d="M10 10.5 L15 16" stroke="#fff" stroke-width="1.8"/></svg>
  </div>
</div>

<!-- Company check -->
<div class="check">
  <div class="check-title">Company Check</div>
  <ul class="check-list">
    <li><svg class="ico" viewBox="0 0 30 30"><circle cx="15" cy="15" r="14" fill="#fff"/><path d="M8 15 L13 20 L22 10" fill="none" stroke="#27ae60" stroke-width="3.5"/></svg><span style="padding-left:4px">Active</span></li>
    <li><svg class="ico" viewBox="0 0 30 30"><circle cx="15" cy="15" r="14" fill="#fff"/><path d="M8 15 L13 20 L22 10" fill="none" stroke="#27ae60" stroke-width="3.5"/></svg><span>Company<br>verified</span></li>
    <li><svg class="ico" viewBox="0 0 30 30"><circle cx="15" cy="15" r="14" fill="#fff"/><path d="M8 15 L13 20 L22 10" fill="none" stroke="#27ae60" stroke-width="3.5"/></svg><span>Verified<br>employee</span></li>
    <li><svg class="ico" viewBox="0 0 30 30"><g fill="#fff"><circle cx="15" cy="3" r="2.6"/><circle cx="23.5" cy="6.5" r="2.3"/><circle cx="27" cy="15" r="2"/><circle cx="23.5" cy="23.5" r="1.7"/><circle cx="15" cy="27" r="1.4"/><circle cx="6.5" cy="23.5" r="1.1"/><circle cx="3" cy="15" r=".9"/><circle cx="6.5" cy="6.5" r="3"/></g></svg><span>Number of<br>verified drivers</span></li>
  </ul>
</div>

<!-- Employee approved -->
<div class="card" style="left:367px;top:233px;width:174px;height:122px">
  <div class="figure-fill" role="img" aria-label="Illustration of an approved driver in a cap" style="left:104px;top:12px;width:62px;height:78px;border-radius:28px 28px 4px 4px"></div>
  <div class="status-row"><span class="stamp">APPROVED</span><svg width="18" height="15" viewBox="0 0 20 16"><path d="M2 8 L7 13 L18 2" fill="none" stroke="#27ae60" stroke-width="3"/></svg></div>
  <div class="abs name" style="left:11px;top:56px">Piet Lander</div>
  <div class="details"><span class="dots"><i></i><i></i><i></i></span>DETAILS</div>
</div>

<!-- Company approved -->
<div class="card" style="left:367px;top:391px;width:174px;height:122px">
  <div class="status-row"><span class="stamp">APPROVED</span><svg width="18" height="15" viewBox="0 0 20 16"><path d="M2 8 L7 13 L18 2" fill="none" stroke="#27ae60" stroke-width="3"/></svg></div>
  <div class="figure-fill" role="img" aria-label="Company building icon" style="left:108px;top:16px;width:54px;height:27px"></div>
  <div class="abs name" style="left:11px;top:55px">Quickhaul</div>
  <div class="figure-fill" role="img" aria-label="Truck icon" style="left:109px;top:53px;width:56px;height:25px"></div>
  <div class="abs" style="left:11px;top:76px;color:var(--green);font-weight:600;font-size:11px">COMPANY DATA</div>
  <div class="details"><span class="dots"><i></i><i></i><i></i></span>DETAILS</div>
</div>

<!-- Drivers -->
<div class="card" style="left:367px;top:539px;width:174px;height:122px">
  <div class="status-row"><span class="stamp">APPROVED</span><svg width="18" height="15" viewBox="0 0 20 16"><path d="M2 8 L7 13 L18 2" fill="none" stroke="#27ae60" stroke-width="3"/></svg></div>
  <div class="abs name" style="left:11px;top:55px">Number of drivers:</div>
  <div class="abs" style="left:33px;top:74px;font-family:'Oswald',sans-serif;font-weight:600;font-size:30px;color:var(--green)">35</div>
  <div class="details" style="right:9px"><span class="dots"><i></i><i></i><i></i></span>DETAILS</div>
</div>

<!-- Rejected -->
<div class="card" style="left:615px;top:196px;width:174px;height:123px">
  <div class="figure-fill" role="img" aria-label="Illustration of a rejected applicant" style="left:104px;top:19px;width:60px;height:72px;border-radius:28px 28px 4px 4px"></div>
  <div class="status-row"><span class="stamp dark">REJECTED</span><svg width="14" height="14" viewBox="0 0 14 14"><path d="M2 2 L12 12 M12 2 L2 12" stroke="#1a1a1a" stroke-width="3"/></svg></div>
  <div class="abs name" style="left:18px;top:56px">Mira Holt</div>
  <div class="details"><span class="dots"><i></i><i></i><i></i></span>DETAILS</div>
</div>

<!-- Company data detail -->
<div class="card" style="left:615px;top:373px;width:174px;height:252px">
  <div class="figure-fill" role="img" aria-label="Company building icon" style="left:58px;top:14px;width:54px;height:27px"></div>
  <div class="data name" style="top:50px">Quickhaul</div>
  <div class="data" style="top:81px"><b>Vat No.</b> 615208437</div>
  <div class="data" style="top:107px"><b>Verified phone no.:</b><br>+32 400 128 706</div>
  <div class="data" style="top:150px"><b>Verified bank No.:</b><br>BE110284736592</div>
  <div class="pill-btn" style="left:7px;top:204px;width:156px;height:35px;font-size:12px">ADD TO THE NETWORK +</div>
</div>

<!-- Conditions -->
<div class="card" style="left:869px;top:41px;width:174px;height:251px">
  <div class="abs" style="left:11px;top:15px;font-weight:600;font-size:13px">Conditions</div>
  <div class="chip" style="top:32px;background:var(--chip-soft)">Location 1</div>
  <svg class="abs" style="left:133px;top:12px" width="27" height="39" viewBox="0 0 27 39"><path d="M13.5 38 C5 24 1 19 1 13 A12.5 12.5 0 0 1 26 13 C26 19 22 24 13.5 38Z" fill="#27ae60"/><circle cx="13.5" cy="13" r="4.5" fill="#fff"/></svg>
  <div class="chip" style="top:71px;background:var(--green);color:var(--white)">Plant 1</div>
  <div class="grey-pill" style="top:110px">Active geofencing<br>required</div>
  <div class="grey-pill" style="top:162px">Verified identity<br>required</div>
  <div class="next-tab">NEXT <svg width="9" height="10" viewBox="0 0 9 10"><path d="M0 0 L9 5 L0 10Z" fill="#fff"/></svg></div>
</div>

<!-- Step 2 -->
<div class="card" style="left:870px;top:349px;width:172px;height:170px">
  <div class="abs step-title" style="left:13px;top:6px">Step 2</div>
  <div class="abs" style="left:0;width:100%;text-align:center;top:29px;font-weight:600;font-size:13px">Gate portal</div>
  <div class="figure-fill" role="img" aria-label="Gate building icon" style="left:58px;top:51px;width:54px;height:27px"></div>
  <div class="plant-pill"><svg style="position:absolute;left:14px;top:6px" width="15" height="21" viewBox="0 0 15 21"><path d="M7.5 20 C3 13 1 10 1 7 A6.5 6.5 0 0 1 14 7 C14 10 12 13 7.5 20Z" fill="#27ae60"/><circle cx="7.5" cy="7" r="2.5" fill="#fff"/></svg>PLANT 1</div>
  <div class="pill-btn" style="left:6px;top:126px;width:156px;height:35px">VERIFIER<svg style="position:absolute;right:16px" width="10" height="12" viewBox="0 0 10 12"><path d="M0 0 L10 6 L0 12Z" fill="#fff"/></svg></div>
</div>

<!-- Gate pass -->
<div class="pass">
  <div class="stamp light" style="left:14px;top:13px">APPROVED</div>
  <div class="gps"><svg width="20" height="29" viewBox="0 0 20 29"><path d="M10 28 C4 19 1 15 1 10 A9 9 0 0 1 19 10 C19 15 16 19 10 28Z" fill="#fff"/><circle cx="10" cy="10" r="3.3" fill="#27ae60"/></svg><div>GPS</div></div>
  <div class="pass-lines">
    <div><b>Driver:</b> Jorn Lander</div>
    <div><b>Company:</b> Quickhaul</div>
    <div><b>Truck:</b> KRL7PX21</div>
    <div><b>Truck:</b> Korvan</div>
    <div><b>Truck color:</b> White</div>
  </div>
  <div class="id-card" role="img" aria-label="Driver ID card icon"></div>
</div>

</body>
</html>
```